Business Card for premium dental clinic

We are a premium dental clinic based in Brasov, Romania with more than 15 year on the market, providing quality dental treatment made by a team of more specialized dentists, working with modern equipment as a solution to beautiful and healthy teeth.

Our current logo for the clinic use 2 square with colors black and gold - dr Ternisu - studio, using family fonts Bodoni, Myriad Pro and Segoe Print.
Depending on the printing we used some gold CMYK background or gold foil picture background or a gold gradient.
We want a business card:
- eye catching business card
- distinguished business card
- premium design
- to keep the color scheme of black and gold
- to attract the customers to spent time reading the information
- modern concept

```html
<!DOCTYPE html>
<html lang="en">
<head>
<meta charset="utf-8">
<title>dr Ternisu studio – Business Card</title>
<link rel="stylesheet" href="https://fonts.googleapis.com/css2?family=Roboto:wght@400;500&family=Roboto+Condensed:wght@400&display=swap">
<style>
  :root {
    --backdrop: #9b9b9b;
    --paper: #f7f7f5;
    --ink: #2b2b2b;
    --muted: #6f6f6f;
    --gold: #f2b51c;
    --gold-deep: #d8921a;
    --gold-light: #f7d35a;
    --black: #151515;
  }
  * { box-sizing: border-box; margin: 0; padding: 0; }
  html, body { width: 1200px; height: 1059px; overflow: hidden; }
  body {
    background: var(--backdrop);
    font-family: "Roboto", Arial, sans-serif;
    position: relative;
  }
  .card {
    position: absolute;
    width: 560px;
    height: 320px;
    background: var(--paper);
    border-bottom: 4px solid var(--gold-deep);
    box-shadow: 0 18px 40px rgba(0,0,0,0.28);
  }
  .card--front { left: 80px; top: 90px; }
  .card--back { left: 560px; top: 630px; }

  .brand {
    position: absolute;
    display: flex;
    align-items: center;
  }
  .brand__square {
    background: linear-gradient(135deg, var(--gold-light), var(--gold) 55%, var(--gold-deep));
  }
  .brand__name {
    font-family: "Roboto Condensed", Arial, sans-serif;
    font-weight: 400;
    color: var(--black);
  }
  .card--front .brand { left: 40px; top: 36px; gap: 14px; }
  .card--front .brand__square { width: 70px; height: 70px; }
  .card--front .brand__name { font-size: 34px; }

  .card--back .brand { left: 50%; top: 50%; transform: translate(-50%, -50%); gap: 22px; }
  .card--back .brand__square { width: 110px; height: 110px; }
  .card--back .brand__name { font-size: 54px; }

  .address {
    position: absolute;
    left: 40px; top: 130px;
    font-size: 15px;
    line-height: 20px;
    color: var(--muted);
    font-style: normal;
  }
  .contacts {
    position: absolute;
    left: 40px; top: 182px;
    list-style: none;
    font-size: 15px;
    color: var(--muted);
  }
  .contacts li { display: flex; align-items: center; gap: 10px; height: 20px; }
  .contacts svg { width: 12px; height: 12px; fill: var(--gold); flex: none; }

  .person {
    position: absolute;
    right: 40px; bottom: 38px;
    text-align: right;
  }
  .person__name { font-size: 26px; font-weight: 500; color: var(--gold); letter-spacing: 1px; }
  .person__role { font-size: 16px; color: var(--ink); margin-top: 2px; }
</style>
</head>
<body>
  <section class="card card--front" aria-label="Business card front">
    <div class="brand">
      <span class="brand__square"></span>
      <span class="brand__name">dr Ternisu</span>
    </div>
    <address class="address">412 Linden Court<br>Brasov, Romania 500123</address>
    <ul class="contacts">
      <li><svg viewBox="0 0 12 12"><path d="M2 1h3l1 3-1.5 1a6 6 0 0 0 2.5 2.5L8 6l3 1v3c0 1-1 1-1 1A9 9 0 0 1 1 2s0-1 1-1z"/></svg>268-410-7723</li>
      <li><svg viewBox="0 0 12 12"><path d="M3 0h6v12H3zM4 1.5v8h4v-8z"/></svg>268-733-1904</li>
      <li><svg viewBox="0 0 12 12"><path d="M2 4h8v6H2zM3 1h6v3H3z"/></svg>268-592-4410</li>
      <li><svg viewBox="0 0 12 12"><path d="M0 2h12v8H0zM1 3l5 3.5L11 3z" fill-rule="evenodd"/></svg>hello@ternisustudio.ro</li>
      <li><svg viewBox="0 0 12 12"><circle cx="6" cy="6" r="5.5"/></svg>www.ternisustudio.ro</li>
    </ul>
    <div class="person">
      <p class="person__name">Daniel Marin</p>
      <p class="person__role">President</p>
    </div>
  </section>

  <section class="card card--back" aria-label="Business card back">
    <div class="brand">
      <span class="brand__square"></span>
      <span class="brand__name">dr Ternisu</span>
    </div>
  </section>
</body>
</html>
```